Home page design for Drone video business (the Business focusses on home videos for realtors)

Dear reader,

*I NEED DESIGNS OF ALL THE PAGES*
We need a first design of a homepage and of 4 other pages of the website of a business that sells drone video services. All the pages will need to be in the similar design style.
The video's are targeted at consumers that want to sell there home and would like to have a cool drone video of photos of their home.

How does the website look:
- has a navbar on top
- A cool looking banner of an areal drone.
- A Big header: with company name: SkyLoftReels
- A smaller subheader: We film your home to increase your chances of sale
- Then a section with a Big header: How does it work
- In this section a place for a vimeo explainitory video
- Then a similar navbar styled bar with a phone number and a email address
- Then a section where the videos porfolio is displayed in a cool way
- Inside this sectiona header: Our work

- A section with header: Why us?
- 4 symbols here with a subheader and some lorum ipsum text underneath (see wireframe images)

- Under that a: Contact us
- where you can put in name, email, phone, message box and a send button

- At the bottom a footer with phone number and a fake address for now.

Be creative. Use creative but serious color.
Use a serious font. Make it a sharp design. Sharp lines. Not to dark design and not to light design.

The wireframes are the same kind of images.
PLEASE PUT IN DESIGNS OF ALL THE PAGES

Good luck

Target Market(s)

People that want to sell home and want to make a cool drone video or photos of their home.

Industry/Entity Type

Business

Contact Information for Business Card

Lucas Wenning
lucas@skyloftreels.example
+31647208351

Logo Text

SkyLoftReels

Number of Pages Required

1 page

Font styles to use
Sans Serif

Requirements
Must have
• All the sections as explained in the instructions.
• The nav bar should have an about us, services, portfolio and a contact us buttons.
• See instruction for details.
• Must include designs of the front page, contact us, our services, portfolio and contact us.
• If you do add some designs for the "about us", "services", "prices", "portfolio" and "contact us" pages, you make a way better chance of winning the competition.
Nice to have
• designs for the other pages as described at the Must haves. You make a better chance of winning if you include them. Look at the wireframes to see the mockups for those pages. think creative about what kind of sections and design should be included in those pages.
Should not have
• bad designs.

```html
<!DOCTYPE html>
<html lang="en">
<head>
<meta charset="utf-8">
<title>SkyLoftReels – Prices</title>
<link href="https://fonts.googleapis.com/css2?family=Lato:wght@400;700&display=swap" rel="stylesheet">
<style>
:root{
  --teal:#0f6b72;
  --teal-dark:#0b6066;
  --ink:#1e1e1e;
  --band:#e6e6e6;
  --card:#f3f3f3;
  --line:#dcdcdc;
  --black:#111;
}
*{margin:0;padding:0;box-sizing:border-box}
html,body{width:953px;height:1200px;overflow:hidden;background:#fff}
body{position:relative;font-family:"Lato",Arial,sans-serif;color:var(--ink)}
.abs{position:absolute}

/* header */
.brand{left:78px;top:28px;display:flex;align-items:center;gap:10px}
.brand-mark{width:22px;height:22px;background:var(--teal)}
.brand-name{font-size:22px;font-weight:700;color:var(--ink)}
.contact-chip{display:flex;align-items:center;gap:8px;font-size:15px;top:11px}
.chip-icon{width:29px;height:29px;border-radius:50%;background:var(--teal);display:flex;align-items:center;justify-content:center}
.main-nav{top:66px;left:393px;display:flex;gap:0;font-size:11.5px;font-weight:700}
.main-nav a{position:absolute;text-decoration:none;color:var(--ink);white-space:nowrap}
.main-nav a.is-home{color:var(--teal)}
.nav-underline{left:731px;top:91px;width:41px;height:3px;background:var(--teal)}

/* hero */
.hero{left:0;top:94px;width:953px;height:266px;background:linear-gradient(180deg,#8fa8b5 0%,#7f6a5a 45%,#6b5548 70%,#4f6b3a 100%)}
.hero-band{left:0;top:291px;width:953px;height:69px;background:rgba(11,96,102,.9);text-align:center;color:#fff}
.hero-title{font-size:31px;font-weight:400;margin-top:6px;letter-spacing:.5px}
.hero-sub{font-size:17.5px;margin-top:1px}

/* breadcrumb */
.crumbs{left:0;top:360px;width:953px;height:31px;background:#f1f1f1;font-size:10px;font-weight:700;color:var(--teal)}
.crumbs-inner{position:absolute;left:99px;top:10px;display:flex;align-items:center;gap:6px}
.crumbs-inner .sep{color:#888;font-weight:400}

.section-title{left:0;top:422px;width:953px;text-align:center;font-size:25px;font-weight:700;color:var(--teal)}

/* price cards */
.plan{background:var(--card);box-shadow:0 2px 6px rgba(0,0,0,.12);border-radius:3px}
.plan-tab{position:absolute;height:41px;background:linear-gradient(180deg,#2a2a2a,#050505);color:#fff;font-size:17px;font-weight:700;display:flex;align-items:center;justify-content:center;box-shadow:0 6px 8px rgba(0,0,0,.25)}
.plan-sub{position:absolute;left:0;width:100%;text-align:center;font-size:12.5px}
.plan-price{position:absolute;left:0;width:100%;height:69px;background:var(--band);display:flex;align-items:center;justify-content:center;gap:22px;color:var(--teal)}
.plan-price .amount{font-size:42px;font-weight:700}
.plan-price .unit{font-size:11.5px;font-weight:700}
.plan-features{position:absolute;left:0;width:100%;list-style:none}
.plan-features li{height:32px;line-height:32px;border-bottom:1px solid var(--line);font-size:11.5px;padding-left:24px}
.plan-features li:last-child{border-bottom:1px solid var(--line)}
.inquire{position:absolute;width:97px;height:31px;background:var(--teal);color:#fff;font-size:13px;display:flex;align-items:center;justify-content:center;box-shadow:0 5px 5px rgba(0,0,0,.18)}

/* footer */
.footer{left:0;top:956px;width:953px;height:209px;background:var(--teal-dark);color:#fff}
.foot-head{position:absolute;top:31px;font-size:14px;font-weight:700}
.foot-head::after{content:"";position:absolute;left:0;top:22px;width:82px;height:1px;background:rgba(255,255,255,.3)}
.foot-divider{position:absolute;top:40px;width:1px;height:140px;background:rgba(0,0,0,.18)}
.quick-links{position:absolute;left:78px;top:57px;list-style:none;font-size:11px}
.quick-links li{height:22px}
.quick-links li::before{content:"› ";font-weight:700}
.contact-list{position:absolute;left:217px;top:60px;font-size:10.5px}
.contact-list .row{display:flex;gap:8px;align-items:flex-start;margin-bottom:17px}
.contact-list b{font-weight:700}
.map{position:absolute;left:445px;top:62px;width:213px;height:120px;background:linear-gradient(135deg,#e2ddd3,#d3cdc2)}
.foot-brand{position:absolute;left:705px;top:110px;display:flex;align-items:center;gap:8px;font-size:18px;font-weight:700;color:#e8eef0}
.foot-brand .sq{width:16px;height:16px;background:#e8eef0}
.bottom-bar{left:0;top:1165px;width:953px;height:35px;background:var(--black);color:#fff;font-size:9px}
.social{position:absolute;top:9px;width:16px;height:16px;border:1px solid #fff;border-radius:50%}
</style>
</head>
<body>

<header>
  <div class="abs brand"><span class="brand-mark"></span><span class="brand-name">SkyLoftReels</span></div>
  <div class="abs contact-chip" style="left:567px">
    <span class="chip-icon"><svg width="14" height="14" viewBox="0 0 24 24"><path fill="#fff" d="M6.6 10.8a15 15 0 0 0 6.6 6.6l2.2-2.2c.3-.3.7-.4 1-.2 1.1.4 2.3.6 3.6.6.6 0 1 .4 1 1V20c0 .6-.4 1-1 1A17 17 0 0 1 3 4c0-.6.4-1 1-1h3.5c.6 0 1 .4 1 1 0 1.3.2 2.5.6 3.6.1.3 0 .7-.2 1z"/></svg></span>
    <span>+316 472 08351</span>
  </div>
  <div class="abs contact-chip" style="left:730px;font-size:13px">
    <span class="chip-icon"><svg width="15" height="11" viewBox="0 0 20 14"><rect x="1" y="1" width="18" height="12" fill="none" stroke="#fff" stroke-width="1.6"/><path d="M1 1l9 7 9-7" fill="none" stroke="#fff" stroke-width="1.6"/></svg></span>
    <span>contact@skyloftreels.example</span>
  </div>
  <nav class="abs main-nav">
    <a class="is-home" style="left:0">HOME</a>
    <a style="left:68px">ABOUT US</a>
    <a style="left:158px">SERVICES</a>
    <a style="left:242px">PORTFOLIO</a>
    <a style="left:340px">PRICES</a>
    <a style="left:412px">CONTACT US</a>
  </nav>
  <div class="abs nav-underline"></div>
</header>

<section class="abs hero" role="img" aria-label="Aerial photo of a brick house with a drone hovering above the roof"></section>
<div class="abs hero-band">
  <h1 class="hero-title">SKYLOFTREELS</h1>
  <p class="hero-sub">We Film Your Home To Increase Your Chances Of Sale</p>
</div>

<div class="abs crumbs">
  <div class="crumbs-inner">
    <svg width="13" height="11" viewBox="0 0 13 11"><path d="M6.5 0L0 5.5h2V11h3.3V7.5h2.4V11H11V5.5h2z" fill="#333"/></svg>
    <span class="sep">/</span><span>PRICES</span>
  </div>
</div>

<h2 class="abs section-title">PRICES</h2>

<!-- hourly -->
<div class="abs plan" style="left:80px;top:495px;width:264px;height:391px">
  <div class="plan-sub" style="top:51px">Lorem Ipsum Dolor</div>
  <div class="plan-price" style="top:75px"><span class="amount">$85</span><span class="unit">Per Hour (no min)</span></div>
  <ul class="plan-features" style="top:155px">
    <li>- Lorem Ipsum is simply dummy text of the.</li>
    <li>- It has survived not only five centuries.</li>
    <li>- Lorem Ipsum is simply dummy text of the.</li>
    <li>- It has survived not only five centuries.</li>
    <li>- Lorem Ipsum is simply dummy text of the.</li>
  </ul>
  <div class="inquire" style="left:85px;top:337px">Inquire</div>
</div>
<div class="plan-tab" style="left:126px;top:488px;width:175px">Hourly Rate</div>

<!-- full day -->
<div class="abs plan" style="left:610px;top:495px;width:265px;height:391px">
  <div class="plan-sub" style="top:49px">Lorem Ipsum Dolor</div>
  <div class="plan-price" style="top:75px"><span class="amount">$600</span><span class="unit">Per Full Day (8 hrs)</span></div>
  <ul class="plan-features" style="top:155px">
    <li>- Lorem Ipsum is simply dummy text of the.</li>
    <li>- It has survived not only five centuries.</li>
    <li>- Lorem Ipsum is simply dummy text of the.</li>
    <li>- It has survived not only five centuries.</li>
    <li>- Lorem Ipsum is simply dummy text of the.</li>
  </ul>
  <div class="inquire" style="left:82px;top:337px">Inquire</div>
</div>
<div class="plan-tab" style="left:653px;top:488px;width:175px">Full Day Rate</div>

<!-- half day -->
<div class="abs plan" style="left:344px;top:475px;width:266px;height:445px;box-shadow:0 3px 10px rgba(0,0,0,.16)">
  <div class="plan-sub" style="top:49px">Lorem Ipsum Dolor</div>
  <div class="plan-price" style="top:75px"><span class="amount">$300</span><span class="unit">Per Half Day (4 hrs)</span></div>
  <ul class="plan-features" style="top:146px">
    <li>- Lorem Ipsum is simply dummy text of the.</li>
    <li>- It has survived not only five centuries.</li>
    <li>- Lorem Ipsum is simply dummy text of the.</li>
    <li>- It has survived not only five centuries.</li>
    <li>- Lorem Ipsum is simply dummy text of the.</li>
    <li>- Lorem Ipsum is simply dummy text of the.</li>
    <li>- It has survived not only five centuries.</li>
  </ul>
  <div class="inquire" style="left:84px;top:394px">Inquire</div>
</div>
<div class="plan-tab" style="left:389px;top:468px;width:175px">Half Day Rate</div>

<footer class="abs footer">
  <h3 class="foot-head" style="left:78px">Quick Links</h3>
  <ul class="quick-links">
    <li>Home</li><li>About Us</li><li>Services</li><li>Portfolio</li><li>Prices</li><li>Contact Us</li>
  </ul>
  <div class="foot-divider" style="left:185px"></div>

  <h3 class="foot-head" style="left:217px">Contact Detail</h3>
  <div class="contact-list">
    <div class="row"><svg width="11" height="15" viewBox="0 0 11 15"><path d="M5.5 0A5.5 5.5 0 0 0 0 5.5C0 9.6 5.5 15 5.5 15S11 9.6 11 5.5A5.5 5.5 0 0 0 5.5 0zm0 7.5a2 2 0 1 1 0-4 2 2 0 0 1 0 4z" fill="#fff"/></svg><span><b>SLR,</b> Lorem ipsum dolor sit amet,<br>consectetuer auyipiscing elit</span></div>
    <div class="row"><svg width="12" height="12" viewBox="0 0 24 24"><path fill="#fff" d="M6.6 10.8a15 15 0 0 0 6.6 6.6l2.2-2.2c.3-.3.7-.4 1-.2 1.1.4 2.3.6 3.6.6.6 0 1 .4 1 1V20c0 .6-.4 1-1 1A17 17 0 0 1 3 4c0-.6.4-1 1-1h3.5c.6 0 1 .4 1 1 0 1.3.2 2.5.6 3.6.1.3 0 .7-.2 1z"/></svg><b>+316 472 08351</b></div>
    <div class="row"><svg width="12" height="12" viewBox="0 0 12 12"><rect x="3" y="0" width="6" height="3" fill="#fff"/><rect x="0" y="4" width="12" height="5" fill="#fff"/><rect x="3" y="8" width="6" height="4" fill="#fff" stroke="#0b6066"/></svg><b>+316 472 08351</b></div>
    <div class="row"><svg width="13" height="10" viewBox="0 0 20 14"><rect x="1" y="1" width="18" height="12" fill="#fff"/><path d="M1 1l9 7 9-7" fill="none" stroke="#0b6066" stroke-width="1.6"/></svg><b>contact@skyloftreels.example</b></div>
  </div>
  <div class="foot-divider" style="left:419px"></div>

  <h3 class="foot-head" style="left:445px">Map</h3>
  <div class="map" role="img" aria-label="Street map with a pin marking 18 Harbour Ln"></div>
  <div class="foot-divider" style="left:682px"></div>

  <div class="foot-brand"><span class="sq"></span>SkyLoftReels</div>
</footer>

<div class="abs bottom-bar">
  <span style="position:absolute;left:78px;top:12px">Copyright © 2016 SkyLoftReels.&nbsp; All Rights Reserved</span>
  <span class="social" style="left:810px"></span>
  <span class="social" style="left:834px"></span>
  <span class="social" style="left:858px"></span>
</div>

</body>
</html>
```